RWT Fittings Ltd Business Cards

We need a business card with our business logo. We provide window and door installations on high-rises in west coast British Colombia, Canada.

I would like my business information and details on one side of the card, and the other side the company name with logo

Target Market(s)

General Contractors

Industry/Entity Type

Construction

Contact Information for Business Card

one side i want my company name and logo in the dark theme logo that i provided

Requirements
Must have
• Marco Peltieri, 16045518293, RWTFittings@mailbox-demo.com, 1407-5194 Linden Row Burnaby BC, V5H 2K9, Owner & Manager

```html
<!DOCTYPE html>
<html lang="en">
<head>
<meta charset="utf-8">
<title>RWT Fittings Ltd – Business Cards</title>
<link rel="stylesheet" href="https://fonts.googleapis.com/css2?family=Roboto:wght@400;500;700;900&display=swap">
<style>
  :root {
    --page-bg: #232323;
    --card-dark: #1f1f23;
    --photo-deep: #1c1a18;
    --photo-warm: #4a423a;
    --brand-blue: #27a9e1;
    --brand-grey: #9a9a9a;
    --text-light: #f2f2f2;
    --text-soft: #cfcfcf;
  }
  * { box-sizing: border-box; margin: 0; padding: 0; }
  html, body {
    width: 1200px; height: 780px; overflow: hidden;
    background: var(--page-bg);
    font-family: "Roboto", Arial, sans-serif;
  }
  .stage {
    width: 1200px; height: 780px;
    display: flex; align-items: center; justify-content: center; gap: 40px;
  }
  .card {
    position: relative;
    width: 540px; height: 310px;
    border-radius: 16px;
    overflow: hidden;
    box-shadow: 0 14px 30px rgba(0,0,0,.55);
  }

  /* Front */
  .card-front .backdrop {
    position: absolute; inset: 0;
    background: radial-gradient(ellipse at 70% 30%, var(--photo-warm) 0%, #34302b 45%, var(--photo-deep) 100%);
  }
  .front-name {
    position: absolute; left: 0; right: 0; top: 50%;
    transform: translateY(-50%);
    display: flex; align-items: center; justify-content: center; gap: 14px;
  }
  .brand-square {
    width: 34px; height: 34px; background: var(--brand-blue);
  }
  .brand-name {
    font-weight: 700; font-size: 40px; color: var(--brand-blue);
    letter-spacing: 1px;
  }

  /* Back */
  .card-back { background: var(--card-dark); }
  .back-brand {
    position: absolute; left: 28px; top: 126px;
    display: flex; align-items: center; gap: 10px;
  }
  .back-brand .brand-square { width: 24px; height: 24px; }
  .back-brand .brand-name { font-size: 26px; }
  .divider {
    position: absolute; left: 300px; top: 50px;
    width: 2px; height: 170px; background: var(--text-light);
  }
  .contact {
    position: absolute; left: 322px; top: 56px; right: 16px;
    color: var(--text-light);
  }
  .person-name { font-weight: 900; font-size: 22px; line-height: 1.05; }
  .person-name .first { color: var(--brand-blue); }
  .person-name .last { color: var(--text-soft); }
  .person-role { font-weight: 700; font-size: 12.5px; margin-top: 2px; }
  .address { font-size: 12px; line-height: 1.35; margin-top: 16px; }
  .lines { list-style: none; margin-top: 14px; font-size: 11.5px; }
  .lines li { display: flex; align-items: center; gap: 7px; line-height: 1.6; white-space: nowrap; }
  .lines svg { width: 12px; height: 12px; flex: none; }
  .band-blue {
    position: absolute; left: 0; bottom: 18px;
    width: 330px; height: 20px; background: var(--brand-blue);
  }
  .band-mark {
    position: absolute; left: 340px; bottom: 22px;
    width: 26px; height: 26px; background: var(--brand-blue);
  }
  .band-grey {
    position: absolute; left: 378px; right: 0; bottom: 46px;
    height: 14px; background: var(--brand-grey);
  }
</style>
</head>
<body>
<main class="stage">
  <section class="card card-front">
    <div class="backdrop" role="img" aria-label="Dimly lit office interior photograph"></div>
    <div class="front-name">
      <span class="brand-square"></span>
      <span class="brand-name">RWT Fittings Ltd</span>
    </div>
  </section>

  <section class="card card-back">
    <div class="back-brand">
      <span class="brand-square"></span>
      <span class="brand-name">RWT Fittings Ltd</span>
    </div>
    <div class="divider"></div>
    <div class="contact">
      <h1 class="person-name"><span class="first">Marco</span> <span class="last">Peltieri</span></h1>
      <p class="person-role">Owner &amp; Manager</p>
      <p class="address">1407-5194 Linden Row<br>Burnaby BC, V5H 2K9</p>
      <ul class="lines">
        <li>
          <svg viewBox="0 0 24 24" aria-hidden="true"><path fill="#27a9e1" d="M6.6 10.8a15.1 15.1 0 0 0 6.6 6.6l2.2-2.2a1 1 0 0 1 1-.25 11.4 11.4 0 0 0 3.6.57 1 1 0 0 1 1 1V20a1 1 0 0 1-1 1A17 17 0 0 1 3 4a1 1 0 0 1 1-1h3.5a1 1 0 0 1 1 1c0 1.25.2 2.45.57 3.57a1 1 0 0 1-.25 1z"/></svg>
          1604 551 8293
        </li>
        <li>
          <svg viewBox="0 0 24 24" aria-hidden="true"><rect x="2" y="5" width="20" height="14" rx="2" fill="#27a9e1"/><path d="M3 6l9 7 9-7" fill="none" stroke="#1f1f23" stroke-width="2"/></svg>
          RWTFittings@mailbox-demo.com
        </li>
      </ul>
    </div>
    <div class="band-grey"></div>
    <div class="band-mark"></div>
    <div class="band-blue"></div>
  </section>
</main>
</body>
</html>
```